Business Card Design

We are a residential half way house for the addict ,the alcoholic and dual diagnosed in recovery.
i house both men and woman age 18+

Industry/Entity Type

Residential

```html
<!DOCTYPE html>
<html lang="en">
<head>
<meta charset="utf-8">
<title>Sober House Business Card</title>
<link rel="stylesheet" href="https://fonts.googleapis.com/css2?family=Anton&family=Roboto+Condensed:wght@300;400&display=swap">
<style>
  :root {
    --page-bg: #e9e6e1;
    --card-red: #b50d1f;
    --card-red-deep: #8f0716;
    --card-white: #ffffff;
    --photo-dark: #0a0a0c;
    --photo-magenta: #d2246a;
    --photo-orange: #f0703a;
    --photo-blue: #3fa3d9;
  }
  html, body {
    margin: 0;
    width: 1200px;
    height: 892px;
    overflow: hidden;
    background: var(--page-bg);
  }
  .card {
    position: absolute;
    left: 100px;
    top: 160px;
    width: 1000px;
    height: 571px;
    overflow: hidden;
    box-shadow: 0 10px 30px rgba(0,0,0,0.25);
    background: var(--card-red);
  }
  .card-art {
    position: absolute;
    inset: 0;
  }
  .card-content {
    position: absolute;
    right: 48px;
    top: 34px;
    text-align: right;
    color: var(--card-white);
    font-family: "Roboto Condensed", sans-serif;
  }
  .company {
    font-family: "Anton", sans-serif;
    font-weight: 400;
    margin: 0;
    line-height: 1.05;
  }
  .company-line1 { display: block; font-size: 60px; }
  .company-line2 { display: block; font-size: 44px; }
  .person-name {
    margin: 22px 0 0;
    font-weight: 300;
    font-size: 66px;
    line-height: 1;
  }
  .person-role, .person-note {
    margin: 4px 0 0;
    font-size: 22px;
    font-weight: 400;
    line-height: 1.1;
  }
  .contact-list {
    list-style: none;
    margin: 30px 0 0;
    padding: 0;
  }
  .contact-item {
    display: flex;
    justify-content: flex-end;
    align-items: center;
    gap: 14px;
    font-size: 26px;
    line-height: 1;
    height: 40px;
  }
  .contact-icon {
    width: 28px;
    height: 28px;
    flex: none;
  }
</style>
</head>
<body>
  <div class="card">
    <svg class="card-art" width="1000" height="571" viewBox="0 0 1000 571">
      <defs>
        <linearGradient id="photoTone" x1="0" y1="0" x2="0.3" y2="1">
          <stop offset="0" stop-color="var(--photo-dark)"/>
          <stop offset="0.38" stop-color="var(--photo-dark)"/>
          <stop offset="0.6" stop-color="var(--photo-magenta)"/>
          <stop offset="0.78" stop-color="var(--photo-orange)"/>
          <stop offset="1" stop-color="var(--photo-blue)"/>
        </linearGradient>
        <linearGradient id="redTone" x1="0" y1="0" x2="1" y2="1">
          <stop offset="0" stop-color="var(--card-red)"/>
          <stop offset="1" stop-color="var(--card-red-deep)"/>
        </linearGradient>
      </defs>
      <rect class="photo-area" role="img" aria-label="Evening photo of the sober house courtyard with colourful lights" x="0" y="0" width="520" height="571" fill="url(#photoTone)"/>
      <path class="red-panel" d="M300 0 Q 470 300 360 571 L1000 571 L1000 0 Z" fill="url(#redTone)"/>
      <path class="divider-curve" d="M300 0 Q 470 300 360 571" fill="none" stroke="var(--card-white)" stroke-width="10"/>
    </svg>

    <div class="card-content">
      <h1 class="company">
        <span class="company-line1">Marisol's</span>
        <span class="company-line2">Family Sober House Inc</span>
      </h1>
      <p class="person-name">Dana Ruiz</p>
      <p class="person-role">Owner</p>
      <p class="person-note">(15 yrs.in recovery)</p>
      <ul class="contact-list">
        <li class="contact-item">(555) 214-0307
          <svg class="contact-icon" viewBox="0 0 28 28"><rect width="28" height="28" rx="5" fill="#fff"/><path d="M9 7c1 0 2 3 2 4s-2 1-1 3 3 4 5 5 2-1 3-1 4 1 4 2-2 3-4 3C12 23 5 16 5 10c0-2 3-3 4-3z" fill="var(--card-red)"/></svg>
        </li>
        <li class="contact-item">(555) 214-0308
          <svg class="contact-icon" viewBox="0 0 28 28"><rect width="28" height="28" rx="5" fill="#fff"/><path d="M9 7c1 0 2 3 2 4s-2 1-1 3 3 4 5 5 2-1 3-1 4 1 4 2-2 3-4 3C12 23 5 16 5 10c0-2 3-3 4-3z" fill="var(--card-red)"/></svg>
        </li>
        <li class="contact-item">(555) 381-7742
          <svg class="contact-icon" viewBox="0 0 28 28"><rect width="28" height="28" rx="5" fill="#fff"/><rect x="9" y="5" width="10" height="6" fill="var(--card-red)"/><rect x="5" y="11" width="18" height="9" rx="2" fill="var(--card-red)"/><rect x="9" y="17" width="10" height="6" fill="var(--card-red)" stroke="#fff" stroke-width="1.5"/></svg>
        </li>
        <li class="contact-item">danaruiz@example.com
          <svg class="contact-icon" viewBox="0 0 28 28"><rect width="28" height="28" rx="5" fill="#fff"/><rect x="5" y="8" width="18" height="12" fill="var(--card-red)"/><path d="M5 8l9 7 9-7M5 20l7-6M23 20l-7-6" fill="none" stroke="#fff" stroke-width="1.5"/></svg>
        </li>
        <li class="contact-item">2840 Palmetto Rd. Bay Harbor,Fla 33099
          <svg class="contact-icon" viewBox="0 0 28 28"><rect width="28" height="28" rx="5" fill="#fff"/><path d="M14 23s-6-7-6-11a6 6 0 0 1 12 0c0 4-6 11-6 11z" fill="var(--card-red)"/><circle cx="14" cy="12" r="2.2" fill="#fff"/></svg>
        </li>
      </ul>
    </div>
  </div>
</body>
</html>
```